Business card design

Hi,
I need to have a business card design based on the current logo.
If competitive I not put it out to everyone.

It can be single of double sided

Target Market(s)

Food businesses

Industry/Entity Type

Food Manufacturing

Contact Information for Business Card

Details will on card will be as follows Name = Marcus Bell Email = Marcus@PanHearth.com.au Phone = 0418563207 Address = 57 Larkin Street , Kelvin Grove QLD 4059 Australia

Font styles to use
Other font styles liked:
• based on two fonts - Adelle & Museo

Requirements
Must have
• Based on the on switch concept

```html
<!DOCTYPE html>
<html lang="en">
<head>
<meta charset="utf-8">
<title>PanHearth Business Card</title>
<link rel="stylesheet" href="https://fonts.googleapis.com/css2?family=Montserrat:wght@400;600;700&family=Zilla+Slab:wght@400&display=swap">
<style>
  :root {
    --backdrop: #d1d5d5;
    --card-white: #eeeeec;
    --card-dark: #2b181b;
    --brand-red: #e31b3c;
    --text-grey: #5a5a5a;
    --text-light: #f4f4f4;
  }
  * { margin: 0; padding: 0; box-sizing: border-box; }
  html, body {
    width: 1200px;
    height: 1051px;
    overflow: hidden;
    background: var(--backdrop);
  }
  .canvas {
    position: relative;
    width: 1200px;
    height: 1051px;
    display: flex;
    align-items: center;
    justify-content: center;
    gap: 48px;
  }
  .card {
    width: 520px;
    height: 318px;
    position: relative;
    box-shadow: 0 18px 40px rgba(0, 0, 0, 0.18);
  }
  .card-front {
    background: var(--card-white);
    border-bottom: 3px solid var(--brand-red);
    font-family: "Montserrat", sans-serif;
  }
  .holder-name {
    position: absolute;
    top: 78px;
    left: 0;
    right: 0;
    text-align: center;
    color: var(--brand-red);
    font-weight: 700;
    font-size: 27px;
    letter-spacing: 0.5px;
    text-transform: uppercase;
  }
  .details {
    position: absolute;
    top: 170px;
    left: 0;
    right: 0;
    display: flex;
    justify-content: center;
    align-items: stretch;
    gap: 22px;
    color: var(--text-grey);
    font-size: 12.5px;
    line-height: 1.55;
    letter-spacing: 0.4px;
  }
  .address { text-align: right; }
  .divider {
    width: 1.5px;
    background: var(--brand-red);
  }
  .contact-list { list-style: none; }
  .contact-list li {
    display: flex;
    align-items: center;
    gap: 7px;
  }
  .contact-icon { width: 11px; height: 11px; flex: none; }
  .card-back {
    background: var(--card-dark);
    border-bottom: 6px solid var(--brand-red);
    display: flex;
    flex-direction: column;
    align-items: center;
    justify-content: center;
  }
  .brand-lockup {
    display: flex;
    align-items: center;
    gap: 14px;
  }
  .brand-dot {
    width: 34px;
    height: 34px;
    border-radius: 50%;
    background: var(--brand-red);
  }
  .brand-name {
    font-family: "Montserrat", sans-serif;
    font-weight: 600;
    font-size: 46px;
    color: var(--text-light);
    letter-spacing: 1px;
  }
  .tagline {
    margin-top: 6px;
    margin-left: 48px;
    font-family: "Zilla Slab", serif;
    font-size: 15px;
    color: var(--text-light);
    letter-spacing: 0.6px;
  }
</style>
</head>
<body>
<main class="canvas">
  <section class="card card-front">
    <h1 class="holder-name">Marcus Bell</h1>
    <div class="details">
      <p class="address">57 Larkin Street<br>Kelvin Grove<br>QLD 4059 Australia</p>
      <span class="divider"></span>
      <ul class="contact-list">
        <li>
          <svg class="contact-icon" viewBox="0 0 24 24" aria-hidden="true"><path fill="#e31b3c" d="M6.6 10.8a15.1 15.1 0 0 0 6.6 6.6l2.2-2.2a1 1 0 0 1 1-.25 11.4 11.4 0 0 0 3.6.57 1 1 0 0 1 1 1V20a1 1 0 0 1-1 1A17 17 0 0 1 3 4a1 1 0 0 1 1-1h3.5a1 1 0 0 1 1 1c0 1.25.2 2.45.57 3.57a1 1 0 0 1-.25 1z"/></svg>
          0418563207
        </li>
        <li>
          <svg class="contact-icon" viewBox="0 0 24 24" aria-hidden="true"><path fill="#e31b3c" d="M2 5h20v14H2z"/><path fill="none" stroke="#eeeeec" stroke-width="2" d="M2 5l10 8 10-8"/></svg>
          Marcus@PanHearth.com.au
        </li>
        <li>
          <svg class="contact-icon" viewBox="0 0 24 24" aria-hidden="true"><circle cx="12" cy="12" r="10" fill="#e31b3c"/><path fill="none" stroke="#eeeeec" stroke-width="1.6" d="M2 12h20M12 2c3 3 3 17 0 20M12 2c-3 3-3 17 0 20"/></svg>
          www.PanHearth.com.au
        </li>
      </ul>
    </div>
  </section>

  <section class="card card-back">
    <div class="brand-lockup">
      <span class="brand-dot"></span>
      <span class="brand-name">PANHEARTH</span>
    </div>
    <p class="tagline">Fresh Meals Made To Order</p>
  </section>
</main>
</body>
</html>
```